Ridge Lass Crew (Flyer)

I want a flyer to advertise my service.
Details below, and logo's to use are attached.

A girls only after school program, 11-14yrs, as OSHC is no longer avail, dedicated to coaching & mentoring our girls into strong, independent young women.

The Brainchild of Rebecca Folwin, Ridge Lass Crew was created to address the growing demand for after school/school holiday supervision for kids moving from primary into high school, when OSHC ceases to exist.
With over 12 years experience mentoring and coaching young women in the corporate world, Bec decided to leave her role as a Director with Tarrant Trust, and follow her passion.
Bec, along with her sister Lorraine, who has over 10 years experience in local communities as a Youth Worker, and is also a qualified Enrolled Nurse, embarked on building a program designed to keep parents happy (by knowing their girls are safe) and dedicated to coaching and mentoring our girls into strong, independent young women.
Open every afternoon and during school holidays, we look to offer;
- Daily meditation
- Healthy snacks
- Dedicated homework time
- Organised group activity, led by qualified instructors (yoga, fitness class, soccer etc)
- Regular guests speakers, addressing issues/concerns for young people today
- SOCIAL MEDIA FREE ZONE

Located 87 Pelham Pde, Baulkham Hills (across from Crestmoor Day Clinic)
Open 3-6pm Monday to Friday

Facebook page: http://fb.example/ridgelasscrew
Email: info@ridgelasscrew.example.au
Mobile: 0455817396

Target Market(s)

Parents of teenage girls, teenage girls 11-14 years

Industry/Entity Type

School

Font styles to use
Sans Serif

Colors
b768aa
e667a6

Requirements
Must have
• What progam is - see brief
• Who runs it
Should not have
• Not be too busy, not overly mature images

```html
<!DOCTYPE html>
<html lang="en">
<head>
<meta charset="utf-8">
<title>Ridge Lass Crew – Flyer</title>
<link rel="stylesheet" href="https://fonts.googleapis.com/css2?family=Cinzel:wght@600;700&family=Cutive+Mono&family=Open+Sans:wght@400;600;700&display=swap">
<style>
  :root {
    --pink: #ef5ddd;
    --pink-label: #f05ee0;
    --violet: #b35be6;
    --violet-text: #b35be6;
    --sky-1: #bfe6f7;
    --sky-2: #7fa8e6;
    --ink: #1c1c28;
    --navy: #27304a;
    --white: #ffffff;
  }
  html, body { margin: 0; padding: 0; overflow: hidden; background: #eeeeee; }
  .flyer {
    position: relative;
    width: 934px;
    height: 1200px;
    overflow: hidden;
    background: var(--white);
    font-family: "Open Sans", Arial, sans-serif;
    color: var(--ink);
  }
  .top-band { position: absolute; left: 0; top: 0; width: 934px; height: 140px; background: var(--pink); }
  .hero-art {
    position: absolute; left: 0; top: 140px; width: 934px; height: 488px;
    background: linear-gradient(135deg, var(--sky-2) 0%, #a9d2f2 45%, var(--sky-1) 70%, #9cc3ef 100%);
  }
  .hero-photo {
    position: absolute; left: 190px; top: 452px; width: 590px; height: 176px;
    background: radial-gradient(ellipse at 50% 60%, #c9a48c 0%, #8a7a78 40%, rgba(120,130,160,0) 75%);
  }
  .logo-panel {
    position: absolute; left: 628px; top: 45px; width: 268px; height: 305px;
    background: var(--white);
  }
  .logo-art {
    position: absolute; left: 22px; top: 18px; width: 224px; height: 270px;
    background: radial-gradient(ellipse at 50% 50%, #d9d6f5 0%, #eeedfb 55%, rgba(255,255,255,0) 80%);
  }
  .logo-name {
    position: absolute; left: 0; top: 118px; width: 268px; text-align: center;
    font-family: "Open Sans", Arial, sans-serif; font-weight: 700; font-size: 30px; line-height: 36px;
    color: var(--pink);
  }
  .tag {
    position: absolute; background: var(--pink-label);
    font-family: "Cinzel", Georgia, serif; font-weight: 700; color: var(--ink);
    text-align: center; white-space: nowrap;
  }
  .tag--girls { left: 84px; top: 243px; width: 400px; height: 57px; font-size: 32px; line-height: 60px; }
  .tag--program { left: 44px; top: 308px; width: 496px; height: 58px; font-size: 32px; line-height: 60px; }
  .tag--age { left: 118px; top: 378px; width: 328px; height: 52px; font-size: 32px; line-height: 56px; }
  .tag-note {
    position: absolute; left: 112px; top: 434px; font-size: 16px; font-weight: 700; color: var(--ink);
  }
  .intro-band {
    position: absolute; left: 0; top: 628px; width: 934px; height: 180px; background: var(--violet);
    text-align: center;
  }
  .intro-band .by {
    position: absolute; left: 0; top: 18px; width: 100%;
    font-family: "Cinzel", Georgia, serif; font-weight: 700; font-size: 19px; color: var(--ink);
  }
  .intro-band .name {
    position: absolute; left: 0; top: 50px; width: 100%;
    font-family: "Cinzel", Georgia, serif; font-weight: 600; font-size: 36px; color: var(--ink); letter-spacing: 1px;
  }
  .intro-band .mission {
    position: absolute; left: 0; top: 98px; width: 100%;
    font-family: "Cutive Mono", "Courier New", monospace; font-size: 26px; line-height: 44px;
    font-variant: small-caps; color: var(--white); letter-spacing: 1px; font-weight: 700;
  }
  .section-head {
    position: absolute; font-size: 24px; font-weight: 700; color: var(--navy);
    padding-left: 26px; border-left: 4px solid var(--violet); line-height: 30px;
  }
  .section-head--who { left: 50px; top: 838px; }
  .section-head--offer { left: 604px; top: 832px; }
  .who-text {
    position: absolute; left: 42px; top: 900px; width: 528px;
    font-size: 16.2px; line-height: 29px; margin: 0;
  }
  .hours-lead {
    position: absolute; left: 28px; top: 1006px; width: 550px; text-align: center;
    font-size: 21px; font-weight: 700; color: var(--violet-text);
  }
  .hours {
    position: absolute; left: 28px; top: 1046px; width: 550px; text-align: center;
    font-family: "Cinzel", Georgia, serif; font-weight: 700; font-size: 21px; color: var(--ink);
  }
  .offer-list {
    position: absolute; left: 608px; top: 872px; width: 326px; margin: 0; padding: 0; list-style: none;
    font-size: 18px; line-height: 31px;
  }
  .offer-list li { position: relative; padding-left: 34px; white-space: nowrap; }
  .offer-list li::before {
    content: ""; position: absolute; left: 4px; top: 10px; width: 8px; height: 8px; border-radius: 50%;
    background: var(--pink);
  }
  .offer-list .sub { display: block; padding-left: 10px; }
  .footer {
    position: absolute; left: 0; top: 1112px; width: 934px; height: 88px; background: var(--violet);
    color: var(--white);
  }
  .footer .address { position: absolute; left: 95px; top: 24px; font-size: 18px; }
  .footer .address small { display: block; font-size: 12.5px; margin-top: 2px; padding-left: 8px; }
  .footer .call { position: absolute; left: 440px; top: 22px; font-size: 20px; }
  .footer .icon { position: absolute; }
  .footer .email-label { position: absolute; right: 46px; top: 6px; font-size: 18px; font-weight: 700; }
  .footer .email { position: absolute; right: 48px; top: 33px; font-size: 17px; font-weight: 600; }
  .footer .social { position: absolute; right: 48px; top: 62px; font-size: 16px; font-weight: 600; }
  .footer .square { position: absolute; right: 24px; top: 64px; width: 16px; height: 16px; background: var(--white); }
</style>
</head>
<body>
<main class="flyer">
  <div class="top-band"></div>
  <div class="hero-art" role="img" aria-label="Soft blue graphic backdrop with a web of fine white lines"></div>
  <div class="hero-photo" role="img" aria-label="Photo of a smiling girl looking up with both palms open"></div>

  <div class="logo-panel">
    <div class="logo-art" role="img" aria-label="Pale silhouette of a girl jumping with arms raised"></div>
    <div class="logo-name">Ridge Lass<br>Crew</div>
  </div>

  <div class="tag tag--girls">A Girls Only</div>
  <div class="tag tag--program">After School Program</div>
  <div class="tag tag--age">For 11-14yrs</div>
  <div class="tag-note">as OSHC is no longer available</div>

  <section class="intro-band">
    <div class="by">The Brainchild of Rebecca Folwin</div>
    <div class="name">Ridge Lass Crew</div>
    <div class="mission">Dedicated to Coaching &amp; Mentoring Our Girls<br>into Strong, Independent Young women</div>
  </section>

  <h2 class="section-head section-head--who" style="margin:0">WHO WE ARE</h2>
  <p class="who-text">The Brainchild of Rebecca Folwin, Ridge Lass Crew was created to address the growing demand for after school/school holiday supervision for kids moving from primary into high school, when OSHC ceases to exist.</p>
  <div class="hours-lead">Open every afternoon &amp; during school holidays</div>
  <div class="hours">3-6pm Monday to Friday</div>

  <h2 class="section-head section-head--offer" style="margin:0">WHAT WE OFFER</h2>
  <ul class="offer-list">
    <li>Daily meditation</li>
    <li>Healthy snacks</li>
    <li>Organised group activity,<span class="sub">(yoga, fitness class, soccer etc.)</span></li>
    <li>Regular guests speakers</li>
    <li>Dedicated homework time</li>
    <li>Social media free zone</li>
  </ul>

  <footer class="footer">
    <svg class="icon" style="left:62px;top:22px" width="20" height="28" viewBox="0 0 20 28" aria-hidden="true">
      <path d="M10 26 C4 17 2 13 2 9.5 A8 8 0 0 1 18 9.5 C18 13 16 17 10 26 Z" fill="none" stroke="#fff" stroke-width="1.6"/>
      <circle cx="10" cy="9.5" r="3" fill="none" stroke="#fff" stroke-width="1.6"/>
    </svg>
    <div class="address">87 Pelham Pde, Baulkham Hills<small>(across from Crestmoor Day Clinic)</small></div>

    <svg class="icon" style="left:400px;top:22px" width="28" height="28" viewBox="0 0 28 28" aria-hidden="true">
      <path d="M7 4 L11 9 L9 12 C10 15 13 18 16 19 L19 17 L24 21 L21 25 C13 25 4 16 4 7 Z" fill="none" stroke="#fff" stroke-width="1.6" stroke-linejoin="round"/>
      <path d="M16 4 A8 8 0 0 1 24 12 M16 8 A4 4 0 0 1 20 12" fill="none" stroke="#fff" stroke-width="1.6"/>
    </svg>
    <div class="call">Call: 0455817396</div>

    <div class="email-label">e-Mail us</div>
    <svg class="icon" style="right:18px;top:8px" width="24" height="22" viewBox="0 0 24 22" aria-hidden="true">
      <path d="M2 9 L12 2 L22 9 V20 H2 Z M2 9 L12 15 L22 9" fill="none" stroke="#fff" stroke-width="1.4"/>
    </svg>
    <div class="email">info@ridgelasscrew.example.au</div>
    <div class="social">http://fb.example/ridgelasscrew</div>
    <div class="square"></div>
  </footer>
</main>
</body>
</html>
```